Presentation Brochure and Sample Box Design for Kovo Slate

Kovo Slate is a colour coated solid aluminium panel that our company supplies to the signage and building cladding industries.
We require an, A4 double-sided folding brochure (swatch book) that folds 3 ways, opening once and then a second time to lay out 3 pages flat.

There should be a front and back cover.

The inside cover should be reserved with text blocks for written information about the panel.

The opposite page on the right when you first open the brochure should have all our Matte PVDF 2mm colours which you will find in the attached PDF of colour swatches and details.

When the brochure is folded out a second time, showing all three inside pages flat, the two inside pages on the right (next to the inside cover with the written information) should show all our FEVE Gloss 1.6mm colours which you will also find in the attached PDF colour book.

This brochure should have a modern and professional feel suitable for presenting to architects and designers.

We also require a box design to contain aluminium samples of all the colours in the range.

Please refer to the template attached for the box dimensions and layout.

The box should tie in with the brochure as a complete package with a modern and professional look suitable for presenting to architects and designers.

Finally we require a small label sticker to be stuck on the back of each sample. On the sticker should be the Kovo Slate logo, a space to put the product code for the sample colour and the phone number 1300 584 362.

To summarise, this package project includes:
1 tri-folding A4 brochure,
1 sample box package design,
1 sample sticker label.

This is our signature new product that we will be marketing to signage installers to create coloured and printed aluminium signs. We are also looking to move further into the building and architectural market place with this product.

Please refer to the attachments for the Kovo Slate logo - the colour swatch book and template for the sample box.
The Kovo Slate logo can be shown in White, Black or Silver.

Target Market(s)

Architects, interior designers, builders and signage installers.

Font styles to use
Serif
Sans Serif

Requirements
Must have
• A modern, neat and professional upmarket look suitable for presenting to architects.
Nice to have
• A slick and classy look that makes you want to take home the box or brochure even if you're not interested in the product.
Should not have
• A cheap, untidy, low market look with too many colours.

```html
<!DOCTYPE html>
<html lang="en">
<head>
<meta charset="utf-8">
<title>Kovo Slate – Colour Coated Solid Aluminium Panel Swatch Brochure</title>
<link rel="stylesheet" href="https://fonts.googleapis.com/css2?family=Arimo:wght@400;500&family=Poppins:wght@400;500;600;700;800&display=swap">
<style>
  :root {
    --page-bg: #d6d6d6;
    --ink-black: #0d0d0d;
    --panel-dark: #161616;
    --panel-mid: #2a2a2a;
    --paper: #ffffff;
    --paper-grey: #e9e9e9;
    --slate-grey: #5f605b;
    --accent-red: #c8202c;
    --accent-yellow: #e8c21a;
    --text-dark: #222222;
    --text-muted: #8a8a8a;
    --heading-font: "Poppins", sans-serif;
    --body-font: "Arimo", sans-serif;
  }
  * { box-sizing: border-box; margin: 0; padding: 0; }
  html, body { width: 1200px; height: 2470px; overflow: hidden; }
  body { background: var(--page-bg); font-family: var(--body-font); position: relative; }

  .panel { position: absolute; width: 367px; height: 760px; overflow: hidden; }
  .spread { position: absolute; left: 50px; width: 1100px; height: 760px; box-shadow: 0 18px 40px rgba(0,0,0,.28); }
  .hero-cover { position: absolute; left: 416px; top: 50px; box-shadow: 0 18px 40px rgba(0,0,0,.3); }
  .outside-spread { top: 850px; }
  .inside-spread { top: 1650px; }

  /* ---------- Front cover ---------- */
  .cover {
    background:
      linear-gradient(115deg, rgba(255,255,255,0) 30%, rgba(255,255,255,.28) 48%, rgba(255,255,255,0) 62%),
      var(--ink-black);
  }
  .cover-photo {
    position: absolute; left: 0; top: 250px; width: 100%; height: 470px;
    background:
      linear-gradient(180deg, rgba(13,13,13,1) 0%, rgba(13,13,13,0) 18%, rgba(13,13,13,0) 75%, rgba(13,13,13,1) 100%),
      linear-gradient(165deg, #1b2360 0%, #232a70 30%, #3a0f18 55%, #6e1620 70%, #1c0a0c 100%);
  }
  .cover-sheen {
    position: absolute; inset: 0;
    background: linear-gradient(100deg, rgba(255,255,255,0) 40%, rgba(255,255,255,.22) 58%, rgba(255,255,255,0) 75%);
  }
  .cover-brand {
    position: absolute; left: 22px; top: 105px; width: 330px;
    font: 600 38px/1 var(--heading-font); letter-spacing: 4px; color: #f2f2f2;
  }
  .cover-title {
    position: absolute; left: 22px; top: 385px;
    font: 800 27px/1.28 var(--heading-font); color: #f0f0f0; text-transform: uppercase;
  }
  .cover-title .first-letter { color: var(--accent-red); }
  .cover-swatch-label {
    position: absolute; left: 26px; top: 700px;
    font: 700 15px/1 var(--heading-font); color: #d8d8d8; letter-spacing: .5px;
  }

  /* ---------- Swatch cards ---------- */
  .swatch {
    position: relative; border-radius: 5px;
    background: linear-gradient(var(--c) 0 70%, var(--paper) 70%);
    box-shadow: 0 2px 5px rgba(0,0,0,.35);
  }
  .swatch-name {
    position: absolute; left: 5px; bottom: 34%;
    font: 600 5.5px/1 var(--heading-font); color: #fff; text-transform: uppercase; white-space: nowrap;
  }
  .swatch.light .swatch-name { color: #555; }
  .swatch-note {
    position: absolute; left: 5px; top: 76%; width: 62%;
    font: 400 4.5px/1.15 var(--body-font); color: var(--text-muted);
  }

  /* ---------- PVDF panel ---------- */
  .pvdf {
    left: 0; top: 0;
    background:
      linear-gradient(105deg, rgba(255,255,255,0) 30%, rgba(255,255,255,.12) 55%, rgba(255,255,255,0) 75%),
      var(--panel-dark);
  }
  .pvdf-kicker {
    position: absolute; left: 110px; top: 48px;
    font: 500 6.5px/1 var(--heading-font); color: #e6e6e6; text-transform: uppercase;
  }
  .pvdf-kicker .first-letter { color: var(--accent-yellow); }
  .pvdf-title {
    position: absolute; left: 50px; top: 60px;
    font: 800 26px/1 var(--heading-font); color: #fff; transform: rotate(-2deg);
  }
  .pvdf-frame {
    position: absolute; left: 30px; top: 115px; width: 307px; height: 605px;
    border: 1px solid rgba(255,255,255,.6); border-radius: 12px;
  }
  .pvdf-grid {
    position: absolute; left: 18px; width: 268px;
    display: grid; grid-template-columns: repeat(4, 58px); grid-auto-rows: 64px; gap: 12px 12px;
  }
  .pvdf-grid.main { top: 25px; }
  .pvdf-divider { position: absolute; left: 28px; top: 278px; width: 250px; height: 1px; background: rgba(255,255,255,.75); }
  .pvdf-grid.limited { top: 300px; }
  .availability-note {
    grid-column: span 2; align-self: center;
    font: 600 9px/1.3 var(--heading-font); color: #e8e8e8; letter-spacing: 1px; text-transform: uppercase;
  }
  .finish-pill {
    position: absolute; left: 60px; top: 706px; width: 175px; height: 20px; margin-left: 35px;
    transform: translateX(-35px);
    border-radius: 10px; background: var(--paper);
    font: 500 6.5px/20px var(--heading-font); color: #444; text-align: center; text-transform: uppercase;
  }

  /* ---------- Back / info panel ---------- */
  .info {
    left: 367px; top: 0; text-align: center;
    background: linear-gradient(90deg, #bdbdbd 0%, #f4f4f4 18%, #ffffff 50%, #f0f0f0 82%, #c4c4c4 100%);
  }
  .tone-bar { position: absolute; left: 119px; top: 80px; width: 128px; height: 30px; display: flex; }
  .tone-bar .tone-black { flex: 0 0 50%; background: var(--ink-black); }
  .tone-bar .tone-slate { flex: 1; background: var(--slate-grey); }
  .info-block { position: absolute; left: 30px; width: 307px; color: var(--text-dark); }
  .info-block.about { top: 235px; }
  .info-block.contact { top: 415px; }
  .info-heading { font: 400 15px/1.3 var(--body-font); text-transform: uppercase; letter-spacing: .3px; margin-bottom: 10px; }
  .info-copy { font: 400 11.5px/1.35 var(--body-font); }
  .info-brand-box {
    position: absolute; left: 125px; top: 580px; width: 92px; height: 66px;
    background: var(--ink-black); color: #fff;
    font: 600 12px/66px var(--heading-font); letter-spacing: 1px; text-align: center;
  }

  .outside-spread .cover { left: 733px; top: 0; }

  /* ---------- Inside spread ---------- */
  .inside-cover {
    left: 0; top: 0;
    background: linear-gradient(180deg, #111 0%, #161616 60%, #0c0c0c 100%);
  }
  .inside-title {
    position: absolute; left: 40px; top: 150px;
    font: 700 16px/1.35 var(--heading-font); color: #fff; text-transform: uppercase;
  }
  .inside-copy {
    position: absolute; left: 38px; width: 300px;
    font: 400 14px/1.3 var(--body-font); color: #f0f0f0;
  }
  .inside-copy.first { top: 300px; }
  .inside-copy.second { top: 410px; }
  .inside-brand-box {
    position: absolute; left: 50px; top: 610px; width: 235px; height: 130px;
    background: #0a0a0a; color: #f4f4f4;
    font: 600 30px/130px var(--heading-font); letter-spacing: 2px; text-align: center;
  }

  .feve-area { position: absolute; left: 367px; top: 0; width: 733px; height: 760px; background: var(--paper); }
  .feve-header {
    position: absolute; left: 22px; top: 22px; width: 690px; height: 64px;
    background: var(--ink-black); color: #fff; padding: 14px 14px 0;
  }
  .feve-kicker { font: 500 6.5px/1 var(--heading-font); text-transform: uppercase; }
  .feve-title { font: 800 27px/1.1 var(--heading-font); margin-top: 4px; }
  .feve-grid {
    position: absolute; top: 108px;
    display: grid; grid-template-columns: repeat(5, 58px); grid-auto-rows: 62px; gap: 12px 11px;
  }
  .feve-grid.left-page { left: 22px; }
  .feve-grid.right-page { left: 388px; }
  .page-fold { position: absolute; left: 366px; top: 0; width: 1px; height: 540px; background: #e2e2e2; }
  .feve-rule { position: absolute; left: 388px; top: 488px; width: 306px; height: 1px; background: #888; }
  .feve-footnote {
    position: absolute; right: 38px; top: 494px;
    font: 500 7px/1 var(--heading-font); color: #444; text-transform: uppercase;
  }

  .metallics-band { position: absolute; left: 0; top: 540px; width: 733px; height: 220px; background: var(--ink-black); }
  .metallics-header {
    position: absolute; left: 12px; top: 16px; width: 700px; height: 48px;
    background: var(--paper); padding: 6px 12px;
  }
  .metallics-title { font: 800 19px/1.1 var(--heading-font); color: #1a1a1a; }
  .metallics-sub { font: 500 6.5px/1.6 var(--heading-font); color: #444; text-transform: uppercase; }
  .metallics-row {
    position: absolute; top: 92px; display: flex; gap: 8px;
  }
  .metallics-row .swatch { width: 46px; height: 62px; }
  .metallics-row.standard { left: 8px; }
  .metallics-row.pearl {
    left: 338px; top: 82px; padding: 10px; border-radius: 8px; background: var(--panel-mid);
  }
  .metallics-footnote {
    position: absolute; right: 20px; top: 194px;
    font: 500 7px/1 var(--heading-font); color: #ddd; text-transform: uppercase;
  }
</style>
</head>
<body>

<!-- Front cover -->
<section class="panel cover hero-cover" aria-label="Front cover">
  <div class="cover-photo" role="img" aria-label="Photograph of a building facade clad in deep blue and red aluminium panels"></div>
  <div class="cover-sheen"></div>
  <div class="cover-brand">KOVO SLATE</div>
  <h1 class="cover-title"><span class="first-letter">C</span>olour coated<br>solid aluminium<br>panel</h1>
  <p class="cover-swatch-label">COLOR SWATCHES_</p>
</section>

<!-- Outside spread -->
<section class="spread outside-spread" aria-label="Outside spread">
  <article class="panel pvdf">
    <p class="pvdf-kicker"><span class="first-letter">C</span>olour coated solid aluminium</p>
    <h2 class="pvdf-title">PVDF MATTE 2MM</h2>
    <div class="pvdf-frame">
      <div class="pvdf-grid main">
        <div class="swatch light" style="--c:#ffffff"><span class="swatch-name">White</span><span class="swatch-note">matte white undercoat</span></div>
        <div class="swatch" style="--c:#111111"><span class="swatch-name">Black</span><span class="swatch-note">matte white undercoat</span></div>
        <div class="swatch" style="--c:#d21f2f"><span class="swatch-name">Red</span><span class="swatch-note">matte white undercoat</span></div>
        <div class="swatch" style="--c:#2a2f8c"><span class="swatch-name">Reflex Blue</span><span class="swatch-note">matte white undercoat</span></div>
        <div class="swatch" style="--c:#f08a6a"><span class="swatch-name">Orange</span><span class="swatch-note">matte white undercoat</span></div>
        <div class="swatch" style="--c:#1d2d5c"><span class="swatch-name">Navy Blue</span><span class="swatch-note">matte white undercoat</span></div>
        <div class="swatch" style="--c:#1c2748"><span class="swatch-name">Galaxy</span><span class="swatch-note">matte white undercoat</span></div>
        <div class="swatch light" style="--c:#e6d8a8"><span class="swatch-name">Ivory</span><span class="swatch-note">matte white undercoat</span></div>
        <div class="swatch" style="--c:#f5c14f"><span class="swatch-name">Mustard</span><span class="swatch-note">matte white undercoat</span></div>
        <div class="swatch" style="--c:#d7404d"><span class="swatch-name">Plum Red</span><span class="swatch-note">matte white undercoat</span></div>
      </div>
      <div class="pvdf-divider"></div>
      <div class="pvdf-grid limited">
        <p class="availability-note">Check<br>availability</p>
        <div class="swatch" style="--c:#3b4049"><span class="swatch-name">Stee Gray</span><span class="swatch-note">matte white undercoat</span></div>
        <div class="swatch" style="--c:#5b6168"><span class="swatch-name">Iron Gray</span><span class="swatch-note">matte white undercoat</span></div>
        <div class="swatch" style="--c:#b9bbbd"><span class="swatch-name">Warm Gray</span><span class="swatch-note">matte white undercoat</span></div>
        <div class="swatch" style="--c:#c9cacc"><span class="swatch-name">Smokey Gray</span><span class="swatch-note">matte white undercoat</span></div>
        <div class="swatch" style="--c:#d8d2c6"><span class="swatch-name">Cream</span><span class="swatch-note">matte white undercoat</span></div>
        <div class="swatch" style="--c:#b3b4b4"><span class="swatch-name">Metallic Silver</span><span class="swatch-note">matte white undercoat</span></div>
        <div class="swatch" style="--c:#6f7174"><span class="swatch-name">Charcoal</span><span class="swatch-note">matte white undercoat</span></div>
        <div class="swatch" style="--c:#d7c49c"><span class="swatch-name">Gold</span><span class="swatch-note">matte white undercoat</span></div>
        <div class="swatch" style="--c:#f2d83a"><span class="swatch-name">Yellow</span><span class="swatch-note">matte white undercoat</span></div>
        <div class="swatch" style="--c:#1656a4"><span class="swatch-name">Blue</span><span class="swatch-note">matte white undercoat</span></div>
      </div>
    </div>
    <p class="finish-pill">Foldable / Matte white undercoat</p>
  </article>

  <article class="panel info">
    <div class="tone-bar"><span class="tone-black"></span><span class="tone-slate"></span></div>
    <div class="info-block about">
      <h3 class="info-heading">Colour coated solid<br>aluminium panel</h3>
      <p class="info-copy">Lorem ipsum dolor sit amet, consectetuer adipiscing elit, sed diam nonummy nibh euismod tincidunt ut laoreet dolore magna aliquam erat volutpat. Ut wisi</p>
    </div>
    <div class="info-block contact">
      <h3 class="info-heading">Contact details</h3>
      <p class="info-copy">Lorem ipsum dolor sit amet, consectetuer adipiscing elit, sed diam nonummy nibh euismod tincidunt ut laoreet dolore magna aliquam erat volutpat. Ut wisi</p>
    </div>
    <div class="info-brand-box">KOVO SLATE</div>
  </article>

  <article class="panel cover" aria-label="Front cover">
    <div class="cover-photo" role="img" aria-label="Photograph of a building facade clad in deep blue and red aluminium panels"></div>
    <div class="cover-sheen"></div>
    <div class="cover-brand">KOVO SLATE</div>
    <h2 class="cover-title"><span class="first-letter">C</span>olour coated<br>solid aluminium<br>panel</h2>
    <p class="cover-swatch-label">COLOR SWATCHES_</p>
  </article>
</section>

<!-- Inside spread -->
<section class="spread inside-spread" aria-label="Inside spread">
  <article class="panel inside-cover">
    <h2 class="inside-title">Colour coated solid<br>aluminium panel</h2>
    <p class="inside-copy first">Lorem ipsum dolor sit amet, consectetuer adipiscing elit, sed diam nonummy nibh euismod tincidunt ut laoreet dolore magna aliquam erat volutpat. Ut wisi</p>
    <p class="inside-copy second">Lorem ipsum dolor sit amet, consectetuer adipiscing elit, sed diam nonummy nibh euismod tincidunt ut laoreet dolore magna aliquam erat volutpat. Ut wisi</p>
    <div class="inside-brand-box">KOVO SLATE</div>
  </article>

  <div class="feve-area">
    <header class="feve-header">
      <p class="feve-kicker">Colour coated solid aluminium foldable / matte white undercoat</p>
      <h2 class="feve-title">FEVE GLOSS 1.6MM</h2>
    </header>
    <div class="page-fold"></div>

    <div class="feve-grid left-page">
      <div class="swatch light" style="--c:#ffffff"><span class="swatch-name">White</span><span class="swatch-note">matte white undercoat</span></div>
      <div class="swatch" style="--c:#111111"><span class="swatch-name">Black</span><span class="swatch-note">matte white undercoat</span></div>
      <div class="swatch" style="--c:#e21e2e"><span class="swatch-name">Red</span><span class="swatch-note">matte white undercoat</span></div>
      <div class="swatch light" style="--c:#f2e21f"><span class="swatch-name">Yellow</span><span class="swatch-note">matte white undercoat</span></div>
      <div class="swatch" style="--c:#1b79b8"><span class="swatch-name">Process Blue</span><span class="swatch-note">matte white undercoat</span></div>
      <div class="swatch" style="--c:#1e2a5a"><span class="swatch-name">Galaxy</span><span class="swatch-note">matte white undercoat</span></div>
      <div class="swatch light" style="--c:#ebdfb4"><span class="swatch-name">Ivory</span><span class="swatch-note">matte white undercoat</span></div>
      <div class="swatch" style="--c:#1fa14d"><span class="swatch-name">Emerald</span><span class="swatch-note">matte white undercoat</span></div>
      <div class="swatch" style="--c:#3cb54a"><span class="swatch-name">Apple Green</span><span class="swatch-note">matte white undercoat</span></div>
      <div class="swatch" style="--c:#e0323d"><span class="swatch-name">Warm Red</span><span class="swatch-note">matte white undercoat</span></div>
      <div class="swatch" style="--c:#1e4e9a"><span class="swatch-name">Patriotic Blue</span><span class="swatch-note">matte white undercoat</span></div>
      <div class="swatch" style="--c:#5c6169"><span class="swatch-name">Iron Gray</span><span class="swatch-note">matte white undercoat</span></div>
      <div class="swatch" style="--c:#9a9a97"><span class="swatch-name">Warm Gray</span><span class="swatch-note">matte white undercoat</span></div>
      <div class="swatch" style="--c:#a6a8ab"><span class="swatch-name">Smoke Gray</span><span class="swatch-note">matte white undercoat</span></div>
      <div class="swatch light" style="--c:#cfc8bb"><span class="swatch-name">Latte</span><span class="swatch-note">matte white undercoat</span></div>
      <div class="swatch" style="--c:#27338a"><span class="swatch-name">Reflex Blue</span><span class="swatch-note">matte white undercoat</span></div>
      <div class="swatch" style="--c:#1f6b45"><span class="swatch-name">Forest Green</span><span class="swatch-note">matte white undercoat</span></div>
      <div class="swatch" style="--c:#f26b35"><span class="swatch-name">Orange</span><span class="swatch-note">matte white undercoat</span></div>
      <div class="swatch" style="--c:#1f2f66"><span class="swatch-name">Navy Blue</span><span class="swatch-note">matte white undercoat</span></div>
      <div class="swatch" style="--c:#1d4f7a"><span class="swatch-name">Lagoon</span><span class="swatch-note">matte white undercoat</span></div>
      <div class="swatch" style="--c:#8cc63f"><span class="swatch-name">Lime Green</span><span class="swatch-note">matte white undercoat</span></div>
      <div class="swatch" style="--c:#4dbb6a"><span class="swatch-name">Spring Green</span><span class="swatch-note">matte white undercoat</span></div>
      <div class="swatch" style="--c:#e8338a"><span class="swatch-name">Fuchsia</span><span class="swatch-note">matte white undercoat</span></div>
      <div class="swatch" style="--c:#d31f30"><span class="swatch-name">Plum Red</span><span class="swatch-note">matte white undercoat</span></div>
      <div class="swatch" style="--c:#343b44"><span class="swatch-name">Steel Grey</span><span class="swatch-note">matte white undercoat</span></div>
    </div>

    <div class="feve-grid right-page">
      <div class="swatch" style="--c:#7d1f33"><span class="swatch-name">Heritage Red</span><span class="swatch-note">matte white undercoat</span></div>
      <div class="swatch" style="--c:#f58232"><span class="swatch-name">Pumpkin</span><span class="swatch-note">matte white undercoat</span></div>
      <div class="swatch" style="--c:#138a96"><span class="swatch-name">Turquoise</span><span class="swatch-note">matte white undercoat</span></div>
      <div class="swatch" style="--c:#2fae4e"><span class="swatch-name">Green</span><span class="swatch-note">matte white undercoat</span></div>
      <div class="swatch" style="--c:#f0a41f"><span class="swatch-name">Mustard</span><span class="swatch-note">matte white undercoat</span></div>
      <div class="swatch" style="--c:#f08ec0"><span class="swatch-name">Pink</span><span class="swatch-note">matte white undercoat</span></div>
      <div class="swatch" style="--c:#159a88"><span class="swatch-name">Mint</span><span class="swatch-note">matte white undercoat</span></div>
      <div class="swatch" style="--c:#135e55"><span class="swatch-name">Teal</span><span class="swatch-note">matte white undercoat</span></div>
      <div class="swatch" style="--c:#6b3434"><span class="swatch-name">Milk Chocolate</span><span class="swatch-note">matte white undercoat</span></div>
      <div class="swatch light" style="--c:#efe23a"><span class="swatch-name">Lemon Meringue</span><span class="swatch-note">matte white undercoat</span></div>
      <div class="swatch" style="--c:#5a4a50"><span class="swatch-name">Aubergine</span><span class="swatch-note">matte white undercoat</span></div>
      <div class="swatch" style="--c:#4a4466"><span class="swatch-name">Midnight Purple</span><span class="swatch-note">matte white undercoat</span></div>
      <div class="swatch" style="--c:#f29d1f"><span class="swatch-name">Tangerine</span><span class="swatch-note">matte white undercoat</span></div>
      <div class="swatch" style="--c:#80878e"><span class="swatch-name">Ash</span><span class="swatch-note">matte white undercoat</span></div>
      <div class="swatch light" style="--c:#cfccc6"><span class="swatch-name">Cream</span><span class="swatch-note">matte white undercoat</span></div>
      <div class="swatch" style="--c:#8a3fa0"><span class="swatch-name">Violet</span><span class="swatch-note">matte white undercoat</span></div>
      <div class="swatch" style="--c:#7a7272"><span class="swatch-name">Mocha</span><span class="swatch-note">matte white undercoat</span></div>
      <div class="swatch" style="--c:#6a37a6"><span class="swatch-name">Purple</span><span class="swatch-note">matte white undercoat</span></div>
      <div class="swatch" style="--c:#a3288f"><span class="swatch-name">Mulberry</span><span class="swatch-note">matte white undercoat</span></div>
      <div class="swatch" style="--c:#231f66"><span class="swatch-name">Royal Blue</span><span class="swatch-note">matte white undercoat</span></div>
      <div class="swatch" style="--c:#8ccbea"><span class="swatch-name">Baby Blue</span><span class="swatch-note">matte white undercoat</span></div>
      <div class="swatch" style="--c:#8c9c8a"><span class="swatch-name">Olive Green</span><span class="swatch-note">matte white undercoat</span></div>
      <div class="swatch" style="--c:#28348c"><span class="swatch-name">Reflex Blue</span><span class="swatch-note">matte white undercoat</span></div>
      <div class="swatch" style="--c:#8b817c"><span class="swatch-name">Stone</span><span class="swatch-note">matte white undercoat</span></div>
      <div class="swatch" style="--c:#5b2a8e"><span class="swatch-name">Violet</span><span class="swatch-note">matte white undercoat</span></div>
    </div>

    <div class="feve-rule"></div>
    <p class="feve-footnote">**Check availability</p>

    <div class="metallics-band">
      <header class="metallics-header">
        <h2 class="metallics-title">METALLICS &amp; PEARLS 1.6MM</h2>
        <p class="metallics-sub">Foldable / Matte white undercoat</p>
      </header>
      <div class="metallics-row standard">
        <div class="swatch" style="--c:#c2b9ad"><span class="swatch-name">Champagne</span><span class="swatch-note">matte white undercoat</span></div>
        <div class="swatch" style="--c:#d3b98a"><span class="swatch-name">Gold</span><span class="swatch-note">matte white undercoat</span></div>
        <div class="swatch" style="--c:#d2d3d4"><span class="swatch-name">Flash Silver</span><span class="swatch-note">matte white undercoat</span></div>
        <div class="swatch" style="--c:#c3c4c5"><span class="swatch-name">Silver</span><span class="swatch-note">matte white undercoat</span></div>
        <div class="swatch" style="--c:#6e6f71"><span class="swatch-name">Charcoal</span><span class="swatch-note">matte white undercoat</span></div>
        <div class="swatch" style="--c:#b4b4b2"><span class="swatch-name">Silver</span><span class="swatch-note">matte white undercoat</span></div>
      </div>
      <div class="metallics-row pearl">
        <div class="swatch light" style="--c:#f4f4f2"><span class="swatch-name">Pearl White</span><span class="swatch-note">matte white undercoat</span></div>
        <div class="swatch" style="--c:#bfb2a8"><span class="swatch-name">Latte</span><span class="swatch-note">matte white undercoat</span></div>
        <div class="swatch" style="--c:#b3b8bd"><span class="swatch-name">Ocean Gray</span><span class="swatch-note">matte white undercoat</span></div>
        <div class="swatch" style="--c:#b6c6d4"><span class="swatch-name">Blue Gray</span><span class="swatch-note">matte white undercoat</span></div>
        <div class="swatch" style="--c:#0f0f0f"><span class="swatch-name">Black</span><span class="swatch-note">matte white undercoat</span></div>
        <div class="swatch" style="--c:#d9a577"><span class="swatch-name">Copper</span><span class="swatch-note">matte white undercoat</span></div>
      </div>
      <p class="metallics-footnote">**Check availability</p>
    </div>
  </div>
</section>

</body>
</html>
```